I need a design that promotes "A peak path hub for runners". services include assessment, massage, physiotherapy, pilates, suspension training, kinesiotaping in any combination.
I would like to bring the design into my website, flyers etc

Target Market(s)

athletes from beginner to elite - any age, male and female

Industry/Entity Type

Shop

Contact Information for Business Card

Peak-Path Hub for Runners
17 Corla Lane, Westmere, Tauranga
021 874 3061
tess.harlow@mailbrook.example

Logo Text

Logo styles of interest
Abstract Logo
Requirements
Nice to have
• Blue colour theme

```html
<!DOCTYPE html>
<html lang="en">
<head>
<meta charset="utf-8">
<title>Peak-Path Hub for Runners – Business Card</title>
<link rel="stylesheet" href="https://fonts.googleapis.com/css2?family=Oswald:wght@700&family=Carlito&family=Arimo&display=swap">
<style>
  :root {
    --card-black: #000000;
    --brand-blue: #3fbdf3;
    --band-blue: #42c0f8;
    --text-white: #ffffff;
  }
  html, body {
    margin: 0;
    padding: 0;
    width: 1200px;
    height: 693px;
    overflow: hidden;
    background: var(--card-black);
  }
  .card {
    position: relative;
    width: 1200px;
    height: 693px;
    background: var(--card-black);
    overflow: hidden;
  }
  .top-rule {
    position: absolute;
    left: 0;
    top: 67px;
    width: 1200px;
    height: 7px;
    background: var(--brand-blue);
  }
  .brand {
    position: absolute;
    left: 0;
    top: 205px;
    width: 1182px;
    display: flex;
    justify-content: center;
    align-items: center;
    gap: 10px;
  }
  .brand-dot {
    width: 58px;
    height: 58px;
    border-radius: 50%;
    background: var(--brand-blue);
    flex: none;
  }
  .brand-name {
    font-family: "Oswald", "Arial Narrow", sans-serif;
    font-weight: 700;
    font-size: 66px;
    line-height: 76px;
    letter-spacing: 3px;
    color: var(--brand-blue);
    text-transform: uppercase;
    margin: 0;
  }
  .details {
    position: absolute;
    left: 0;
    width: 1182px;
    text-align: center;
    font-family: "Carlito", "Calibri", sans-serif;
    font-size: 38px;
    color: var(--brand-blue);
    margin: 0;
    line-height: 46px;
  }
  .contact-name { top: 310px; }
  .street { top: 367px; }
  .suburb { top: 426px; }
  .website { top: 494px; }
  .contact-band {
    position: absolute;
    left: 0;
    top: 562px;
    width: 1200px;
    height: 80px;
    background: var(--band-blue);
    font-family: "Arimo", "Arial", sans-serif;
    font-size: 38px;
    color: var(--text-white);
  }
  .phone {
    position: absolute;
    left: 60px;
    top: 18px;
    margin: 0;
    line-height: 44px;
  }
  .email {
    position: absolute;
    right: 56px;
    top: 16px;
    margin: 0;
    line-height: 44px;
  }
</style>
</head>
<body>
  <div class="card">
    <div class="top-rule"></div>

    <div class="brand">
      <span class="brand-dot"></span>
      <h1 class="brand-name">Peak-Path Hub for Runners</h1>
    </div>

    <p class="details contact-name">Tess Harlow</p>
    <p class="details street">17 Corla Lane,</p>
    <p class="details suburb">Westmere,Tauranga,</p>
    <p class="details website">www.peakpathhub4runners.example</p>

    <div class="contact-band">
      <p class="phone">Phone 021 874 3061</p>
      <p class="email">tess.harlow@mailbrook.example</p>
    </div>
  </div>
</body>
</html>
```